Updated website design needed for Radiology Group, Pine Hollow Imaging Partners

Clean, uncluttered, updated design needed for top regional Radiology Center. Focus on personal, patient oriented design, (not clinical). Should be simple and easy to navigate, with clear CTAs. Use blues, greens and photos of people in the Central Oregon outdoors.
Uncoded, PSD design only. 2 pages: Home page and one example interior page.
reference current site: http://www.phipclinic-example.com/
Sites they like:
http://www.valescanlabs-example.com/
http://www.tbmx-example.net/handler.cfm?event=practice,main
http://www.kestrelbonecare-example.com/

Medical Imaging

2 page

Sans Serif

• Personal and patient friendly.
• Lots of white space, clean and uncluttered. Clear CTAs, such as: Patient Bill Pay, Make an Appointment, Meet Our Doctors
• Use copy and contact information from the current site.
• Use outdoor images from Central Oregon, late Winter/ Spring (snow, light colors, spring green, for example)
• Include one example interior page, either Your Exam or Meet Our Doctors
• The client likes:
• Meet Our Doctors slider section, and big, easy to navigate Information Center on www.kestrelbonecare-example.com
• The personal feel of the Your Exam section on www.valescanlabs-example.com
• Blues and Greens, outdoorsy imagery
• The client does not like:
• complex drop down menus
• clinical feel
• Do not use lorum ipsum or dummy text.
• Do not use outdoor images from other regions. Do not use Summer (hot, poolside) or Fall (red/orange leaves) images.

```html
<!DOCTYPE html>
<html lang="en">
<head>
<meta charset="utf-8">
<title>Pine Hollow Imaging Partners</title>
<link href="https://fonts.googleapis.com/css2?family=Open+Sans:wght@400;600;700&family=Raleway:wght@400;500&family=Ubuntu:wght@700&display=swap" rel="stylesheet">
<style>
:root{
  --blue:#3a98f7;
  --blue-light:#5cb6fb;
  --green:#45d675;
  --ink:#44535e;
  --text:#7a848c;
  --dark:#333;
  --pale:#f5f5f5;
  --white:#fff;
}
*{margin:0;padding:0;box-sizing:border-box}
html,body{width:739px;height:1200px;overflow:hidden;background:var(--white)}
body{font-family:"Open Sans",sans-serif;color:var(--text);position:relative}
.abs{position:absolute}
.btn{position:absolute;background:var(--green);color:var(--white);font-size:7.5px;display:flex;align-items:center;justify-content:center;text-decoration:none}
.brand{display:flex;align-items:center;gap:4px}
.brand-mark{width:15px;height:15px;background:#8f95c9}
.brand-name{font-size:7px;font-weight:600;color:#4a4f7a;line-height:1.15;width:62px}

.header{top:0;left:0;width:739px;height:39px}
.bill{left:483px;top:16px;font-size:7.5px;color:#555}
.nav{top:39px;left:0;width:739px;height:27px;background:var(--blue)}
.nav a{position:absolute;top:0;height:27px;line-height:27px;color:var(--white);font-size:7px;text-decoration:none}
.nav .active{background:var(--green);width:55px;left:54px;text-align:center}

.hero{top:66px;left:0;width:739px;height:293px}
.hero-panel{position:absolute;left:0;top:0;width:330px;height:293px;background:linear-gradient(180deg,var(--blue-light),var(--blue));text-align:center;color:var(--white)}
.hero-title{position:absolute;top:61px;left:20px;width:290px;font-family:"Raleway",sans-serif;font-size:18.5px;line-height:26px;font-weight:400}
.hero-copy{position:absolute;top:127px;left:30px;width:250px;font-size:7.9px;line-height:13.7px}
.hero-photo{position:absolute;left:330px;top:0;width:409px;height:293px;
  background:
    radial-gradient(ellipse 90px 150px at 82% 55%,rgba(40,60,120,.55),rgba(40,60,120,0) 70%),
    radial-gradient(ellipse 60px 110px at 45% 62%,rgba(60,90,170,.45),rgba(60,90,170,0) 70%),
    linear-gradient(180deg,#b9c3c6 0%,#a8b1ae 28%,#5f6a55 38%,#8f8a66 48%,#b8a27a 72%,#a08866 100%)}
.scroll-down{position:absolute;left:314px;top:231px;width:28px;height:28px;border-radius:50%;background:var(--white);box-shadow:0 1px 3px rgba(0,0,0,.2)}

.about{top:359px;left:0;width:739px;height:236px;background:var(--pale)}
.about-photo{position:absolute;left:55px;top:27px;width:296px;height:164px;
  background:
    radial-gradient(ellipse 70px 90px at 14% 70%,rgba(150,170,200,.6),rgba(150,170,200,0) 75%),
    radial-gradient(ellipse 90px 80px at 62% 95%,rgba(120,150,200,.55),rgba(120,150,200,0) 75%),
    linear-gradient(110deg,#d9d6d2 0%,#c8c2ba 25%,#ece8e1 55%,#f6f3ee 100%)}
.about-card{position:absolute;left:285px;top:37px;width:397px;height:174px;background:var(--white)}
.section-title{font-family:"Ubuntu",sans-serif;font-weight:700;color:var(--ink);font-size:17.5px;line-height:17px;letter-spacing:.3px}
.about-copy{position:absolute;left:385px;top:110px;width:292px;font-size:7.1px;line-height:13.7px}

.doctors{top:595px;left:0;width:739px;height:222px}
.doc-list{position:absolute;right:408px;top:75px;width:300px;text-align:right;font-size:7.1px;line-height:13.7px}
.doc-list b{font-weight:700;color:#888}
.doc-photo{position:absolute;left:366px;top:26px;width:296px;height:164px;
  background:
    radial-gradient(ellipse 95px 60px at 48% 100%,rgba(40,100,200,.85),rgba(40,100,200,0) 80%),
    linear-gradient(180deg,#b7c9dd,#c7d6e6 50%,#a9bed6)}
.arrow{position:absolute;width:26px;height:18px}

.reviews{top:817px;left:0;width:739px;height:201px;background:var(--pale);text-align:center}
.avatar{position:absolute;border-radius:50%}
.reviewer{position:absolute;top:138px;width:739px;font-size:8.8px;color:var(--dark)}
.quote{position:absolute;top:153px;left:230px;width:279px;font-size:7.7px;line-height:13.7px;color:#666}

.footer{top:1018px;left:0;width:739px;height:153px}
.divider{position:absolute;top:19px;width:1px;height:104px;background:#eee}
.foot-text{position:absolute;left:73px;top:62px;width:126px;font-size:7px;line-height:12px;color:#666}
.foot-head{position:absolute;top:22px;font-size:11px;font-weight:400;color:var(--dark)}
.foot-list{position:absolute;top:49px;list-style:none;font-size:7px;line-height:13.7px;color:#555}
.foot-list li::before{content:"•";margin-right:3px}
.contact{position:absolute;left:523px;top:46px;font-size:7.6px;color:#555;list-style:none}
.contact li{height:18px;display:flex;align-items:center;gap:5px}
.contact .tag{color:var(--blue)}
.copyright{top:1171px;left:0;width:739px;height:29px;background:var(--blue);color:var(--white);font-size:7.5px;text-align:center;line-height:29px}
</style>
</head>
<body>

<header class="abs header">
  <div class="abs brand" style="left:55px;top:7px">
    <div class="brand-mark"></div>
    <div class="brand-name">Pine Hollow Imaging Partners</div>
  </div>
  <div class="abs bill">Patient Bill Pay</div>
  <a class="btn" style="left:548px;top:9px;width:91px;height:22px">Meet Our Doctors</a>
</header>

<nav class="abs nav">
  <a class="active">Home</a>
  <a style="left:130px">About Us</a>
  <a style="left:182px">Our Services</a>
  <a style="left:244px">For Patients</a>
  <a style="left:304px">Our Physicians</a>
  <a style="left:374px">For Physicians</a>
  <a style="left:442px">PACS &amp; Document</a>
  <a style="left:523px">Appointments</a>
  <a style="left:593px">Our Locations</a>
</nav>

<section class="abs hero">
  <div class="hero-panel">
    <h1 class="hero-title">Welcome to Pine Hollow Imaging Partners</h1>
    <p class="hero-copy">Pine Hollow Imaging Partners is a diagnostic imaging corporation providing professional services to Central and Eastern Oregon hospitals and clinics as well as state-of-the-art services in its' own outpatient imaging center.</p>
    <a class="btn" style="left:98px;top:191px;width:109px;height:22px;font-size:7.9px">Make an Appointment</a>
  </div>
  <div class="hero-photo" role="img" aria-label="Smiling runners on a dusty outdoor trail race under a pale sky"></div>
  <div class="scroll-down">
    <svg width="28" height="28" viewBox="0 0 28 28"><path d="M10 12l4 4 4-4" fill="none" stroke="#777" stroke-width="1.3"/></svg>
  </div>
</section>

<section class="abs about">
  <div class="about-photo" role="img" aria-label="Smiling physician in a white coat talking with an older patient"></div>
  <div class="about-card"></div>
  <svg class="abs" style="left:360px;top:0" width="12" height="82"><line x1="6" y1="0" x2="6" y2="74" stroke="#999" stroke-width=".8"/><circle cx="6" cy="77" r="2.5" fill="#fff" stroke="#999" stroke-width=".8"/></svg>
  <h2 class="abs section-title" style="left:385px;top:68px">WHAT<br>WE DO?</h2>
  <p class="about-copy">Our state-of-the-art outpatient imaging center provides professional services to Central Oregon Hospitals and Clinics. Pine Hollow Imaging is staffed with fellowship trained physicians with expertise in diagnostic and interventional procedures.</p>
  <a class="btn" style="left:386px;top:162px;width:68px;height:27px">Read More</a>
</section>

<section class="abs doctors">
  <h2 class="abs section-title" style="right:409px;top:30px;text-align:right">MEET<br>OUR DOCTORS</h2>
  <div class="doc-list">
    <b>Specialty</b>- Neuroradiology, Diagnostic Radiology<br>
    <b>Certification</b>- National Board of Radiology 2012, and National Board of Radiology CAQ Neuroradiology 2014<br>
    <b>Medical School</b>- Westbrook Medical School, 2007<br>
    <b>Residency</b>- Westbrook Medical School, 2012<br>
    Fellowship- Neuroradiology-Summit State University, 2014
  </div>
  <a class="btn" style="left:253px;top:158px;width:78px;height:27px">Meet the Doctor</a>
  <div class="doc-photo" role="img" aria-label="Portrait of a smiling radiologist in a blue shirt and dark tie"></div>
  <svg class="arrow" style="left:353px;top:100px" viewBox="0 0 26 18"><rect width="26" height="18" fill="#3a98f7"/><path d="M18 9H8m3-3l-3 3 3 3" fill="none" stroke="#fff" stroke-width=".9"/></svg>
  <svg class="arrow" style="left:651px;top:100px" viewBox="0 0 26 18"><rect width="26" height="18" fill="#45d675"/><path d="M8 9h10m-3-3l3 3-3 3" fill="none" stroke="#fff" stroke-width=".9"/></svg>
</section>

<section class="abs reviews">
  <svg class="arrow" style="left:200px;top:74px" viewBox="0 0 26 18"><rect width="26" height="18" fill="#45d675"/><path d="M18 9H8m3-3l-3 3 3 3" fill="none" stroke="#fff" stroke-width=".9"/></svg>
  <svg class="arrow" style="left:519px;top:74px" viewBox="0 0 26 18"><rect width="26" height="18" fill="#3a98f7"/><path d="M8 9h10m-3-3l3 3-3 3" fill="none" stroke="#fff" stroke-width=".9"/></svg>
  <svg class="abs" style="left:249px;top:35px" width="244" height="106" viewBox="0 0 244 106">
    <circle cx="44" cy="44" r="41" fill="#fff" stroke="#dfeef0" stroke-width="2"/>
    <circle cx="200" cy="44" r="41" fill="#fff" stroke="#e2eefa" stroke-width="2"/>
  </svg>
  <div class="avatar" role="img" aria-label="Faded portrait of a smiling man in a suit" style="left:256px;top:45px;width:76px;height:76px;background:radial-gradient(circle at 50% 35%,#e9e6e3,#d9d9da 60%,#cfd0d2)"></div>
  <div class="avatar" role="img" aria-label="Faded portrait of a smiling woman" style="left:412px;top:45px;width:76px;height:76px;background:radial-gradient(circle at 50% 35%,#ece7e3,#dcdcdc 60%,#d0d0d0)"></div>
  <svg class="abs" style="left:318px;top:22px" width="106" height="106" viewBox="0 0 106 106">
    <path d="M53 2A51 51 0 0 1 104 53A51 51 0 0 1 28 97" fill="none" stroke="#3a98f7" stroke-width="2.5"/>
    <path d="M53 2A51 51 0 0 0 28 97" fill="none" stroke="#45d675" stroke-width="2.5"/>
    <path d="M53 2A51 51 0 0 1 96 26" fill="none" stroke="#45d675" stroke-width="2.5"/>
    <circle cx="53" cy="53" r="47" fill="#fff"/>
  </svg>
  <div class="avatar" role="img" aria-label="Portrait of the reviewer, a man in a grey suit" style="left:325px;top:29px;width:92px;height:92px;background:radial-gradient(ellipse 40px 50px at 50% 100%,#3e3e40,rgba(62,62,64,0) 90%),linear-gradient(180deg,#c2c2c2,#8e8e8e)"></div>
  <div class="reviewer">Daniel Brooks / CEO</div>
  <p class="quote">"I couldn't believe how smoothly it went. I'm a new man. It's wonderful to have all that freedom without pain anymore."</p>
</section>

<footer class="abs footer">
  <div class="abs brand" style="left:73px;top:24px">
    <div class="brand-mark"></div>
    <div class="brand-name">Pine Hollow Imaging Partners</div>
  </div>
  <p class="foot-text">Pine Hollow Imaging Partners is a state-of-the-art Outpatient Imaging Center providing Professional Services to Central Oregon Hospitals and Clinics as well as providing services in its' own outpatient clinic.</p>
  <div class="divider" style="left:210px"></div>
  <div class="divider" style="left:353px"></div>
  <div class="divider" style="left:507px"></div>
  <h3 class="foot-head" style="left:225px">For Patients</h3>
  <ul class="foot-list" style="left:226px">
    <li>About Your Visit</li><li>Why Choose Us?</li><li>Patient Forms</li><li>Billing and Insurance</li><li>Locations and Maps</li><li>Appointments</li>
  </ul>
  <h3 class="foot-head" style="left:378px">Quick Links</h3>
  <ul class="foot-list" style="left:379px;top:47px">
    <li>Home</li><li>About Us</li><li>Our Physicians</li><li>For Physicians</li><li>Disclaimer</li><li>HIPAA</li><li>Log-In</li>
  </ul>
  <h3 class="foot-head" style="left:523px">Contact Us</h3>
  <ul class="contact">
    <li><svg width="8" height="8" viewBox="0 0 24 24"><path d="M6.6 10.8a15 15 0 0 0 6.6 6.6l2.2-2.2a1 1 0 0 1 1-.2 11 11 0 0 0 3.6.6 1 1 0 0 1 1 1V20a1 1 0 0 1-1 1A17 17 0 0 1 3 4a1 1 0 0 1 1-1h3.5a1 1 0 0 1 1 1 11 11 0 0 0 .6 3.6 1 1 0 0 1-.3 1z" fill="#999"/></svg><span>(555) 210-4410 - <span class="tag">Main Line</span></span></li>
    <li><svg width="8" height="8" viewBox="0 0 24 24"><path d="M6.6 10.8a15 15 0 0 0 6.6 6.6l2.2-2.2a1 1 0 0 1 1-.2 11 11 0 0 0 3.6.6 1 1 0 0 1 1 1V20a1 1 0 0 1-1 1A17 17 0 0 1 3 4a1 1 0 0 1 1-1h3.5a1 1 0 0 1 1 1 11 11 0 0 0 .6 3.6 1 1 0 0 1-.3 1z" fill="#999"/></svg><span>(555) 210-4425 - <span class="tag">Scheduling</span></span></li>
    <li><svg width="8" height="8" viewBox="0 0 24 24"><path d="M6.6 10.8a15 15 0 0 0 6.6 6.6l2.2-2.2a1 1 0 0 1 1-.2 11 11 0 0 0 3.6.6 1 1 0 0 1 1 1V20a1 1 0 0 1-1 1A17 17 0 0 1 3 4a1 1 0 0 1 1-1h3.5a1 1 0 0 1 1 1 11 11 0 0 0 .6 3.6 1 1 0 0 1-.3 1z" fill="#999"/></svg><span>(555) 210-4470 - <span class="tag">Billing</span></span></li>
    <li><svg width="8" height="8" viewBox="0 0 24 24"><path d="M6.6 10.8a15 15 0 0 0 6.6 6.6l2.2-2.2a1 1 0 0 1 1-.2 11 11 0 0 0 3.6.6 1 1 0 0 1 1 1V20a1 1 0 0 1-1 1A17 17 0 0 1 3 4a1 1 0 0 1 1-1h3.5a1 1 0 0 1 1 1 11 11 0 0 0 .6 3.6 1 1 0 0 1-.3 1z" fill="#999"/></svg><span>(555) 210-4498 - <span class="tag">Medical Records</span></span></li>
  </ul>
</footer>

<div class="abs copyright">Copyright 2016 Radiology. All right reserved.</div>

</body>
</html>
```